Web Design Project

Psychotherapy and Counselling Practice needs a landing page web design.

My business "Larkfield Advisory" specialises in the treatment of Anxiety and Depression with a holistic approach, endeavouring to unlock the key that holds us to ransom in a life that is imbalanced, frustrating, and ultimately of our own making due to our own perceptions and behaviours.

There is much that impacts us which we cannot change, but we are always in control of how we think, and how we frame our experiences.....learning to challenge those thoughts and behaviours that are destructive and disempowering opens up a world of joyful possibility. Life is about making choices, learn to make wiser and healthier choices.......

Larkfield Advisory has a client base of individual clients but will seek to expand to offer services to the Corporate world by offering an adjunct to employers for established "Wellness Programs".

Larkfield Advisory is a highly professional, ethically bound business, with the needs of the client at the forefront of all we do.

Larkfield Advisory wishes to avoid the usual "jargon driven" psychobabble offered on many counselling web pages. It aims to be stylishly presented, clean in look and with as few "words" as possible and a largely white background (faster loading and more powerful impact of what is stated), those words contained in the webpage should be meaningful, persuasive and have an impact simply at glance. Larkfield does not want , or expect, those prospective clients in need of support , to be reading through volumes of industry driven cliches.

At this point Larkfield is just looking for a high quality landing page. However in time this will likely expand to include other sections such as case studies, video content etc.

Target Market(s)

Those in need of emotional support, suffering mental health issues, and those simply wanting to become self aware supported by a mindful therapist.

Industry/Entity Type

Industry

Requirements
Must have
• The design must incorporate the Larkfield logo and colour schemes found on the attached files.

```html
<!DOCTYPE html>
<html lang="en">
<head>
<meta charset="utf-8">
<title>Larkfield Advisory</title>
<link href="https://fonts.googleapis.com/css2?family=Open+Sans:wght@400;600;700&display=swap" rel="stylesheet">
<style>
:root{
  --header-grey:#6e6e70;
  --green:#7f9c2a;
  --green-light:#b5cf1a;
  --green-dark:#5e7d12;
  --green-text:#5f7a1e;
  --page-bg:#ececec;
  --panel:#ffffff;
  --text:#555;
  --muted:#999;
  --link-green:#c2d27a;
  --dark:#2e2e2e;
}
*{margin:0;padding:0;box-sizing:border-box}
html,body{width:913px;height:1200px;overflow:hidden}
body{position:relative;background:var(--page-bg);font-family:"Open Sans",sans-serif;color:var(--text)}
.abs{position:absolute}

.site-header{left:0;top:0;width:913px;height:98px;background:var(--header-grey)}
.brand{left:98px;top:56px;color:#a9c93a;font-size:20px;font-weight:400;letter-spacing:1px}
.brand-sub{left:99px;top:80px;color:#fff;font-size:9px;letter-spacing:6px}
.phone{right:99px;top:60px;color:#fff;font-size:15px;font-weight:600}
.email{right:99px;top:80px;color:#fff;font-size:10px}

.main-nav{left:0;top:98px;width:913px;height:47px;background:linear-gradient(#dbe82a 0%,#a3c11a 12%,#7c9c14 100%)}
.main-nav ul{list-style:none;position:absolute;left:128px;top:14px;display:flex;gap:27px}
.main-nav li{color:#fff;font-size:14px}
.search{left:614px;top:111px;width:187px;height:19px;background:#fff;border:1px solid #ddd;font-size:7px;color:#aaa;padding:4px 7px}
.search svg{position:absolute;right:4px;top:3px}

.hero{left:0;top:145px;width:913px;height:315px;background:radial-gradient(ellipse at 64% 30%,#f3e38e 0%,#c9a13f 18%,#6a6a24 45%,#2f3a17 80%)}
.hero-title{left:115px;top:258px;color:#fff;font-size:44px;line-height:42px;font-weight:400}
.hero-title span{font-size:34px}
.dots{left:434px;top:421px;display:flex;gap:2px}
.dots i{width:10px;height:10px;border-radius:50%;background:#555;border:1px solid #ddd;display:block}
.dots i:first-child{background:#eee;border-color:#666}

.content-panel{left:91px;top:448px;width:731px;height:530px;background:var(--panel);box-shadow:0 1px 3px rgba(0,0,0,.15)}

.service{top:483px;width:228px;height:117px}
.service .label{position:absolute;left:0;top:78px;width:228px;height:32px;background:var(--green);color:#fff;font-size:12.5px;text-align:center;line-height:32px}
.s1{left:99px;background:linear-gradient(#e8e4dc,#c9b79a)}
.s1 .label{top:79px}
.s2{left:342px;background:linear-gradient(#3c6fb2,#9db8cf 60%,#8a8578)}
.s2 .label{top:78px}
.s3{left:585px;background:linear-gradient(135deg,#c8b21c,#7a8e1a 50%,#5c84c4)}
.s3 .label{top:78px}

.welcome{left:99px;top:614px;width:471px;height:140px;background:linear-gradient(90deg,#5a5a5a 0%,#222 30%,#000 55%)}
.welcome-sub{left:327px;top:668px;color:#fff;font-size:13px}
.welcome-title{left:327px;top:683px;color:#fff;font-size:22px}
.welcome-title span{color:#a7c13a}
.intro{left:99px;top:760px;width:472px;font-size:9.6px;line-height:15.2px;text-align:justify;color:#555}
.intro b{color:var(--green-text);font-weight:600}

.news{left:586px;top:614px;width:228px;height:234px;background:#f0f0f0}
.news h3{position:absolute;left:15px;top:12px;font-weight:400;font-size:12.5px;color:var(--green-text)}
.news-item{position:absolute;left:14px;width:200px}
.news-thumb{position:absolute;left:0;top:0;width:65px;height:52px}
.news-body{position:absolute;left:71px;top:-3px;width:126px}
.news-body h4{font-weight:400;font-size:9px;color:#444;margin-bottom:4px}
.news-body p{font-size:7.4px;line-height:13.7px;color:var(--muted);text-align:justify}
.news-body a{display:block;text-align:right;font-size:7.4px;color:var(--link-green);margin-top:2px;text-decoration:none}

.newsletter{left:99px;top:876px;width:715px;height:80px;background:linear-gradient(#b7cb3a,#8aa31c 55%,#6a8a12);border-radius:2px}
.nl-title{left:128px;top:897px;color:#fff;font-size:15px}
.nl-sub{left:129px;top:921px;color:#fff;font-size:9px}
.nl-input{left:360px;top:900px;width:341px;height:31px;background:#fff;font-size:8px;color:#999;padding:11px 13px}
.nl-submit{left:715px;top:901px;width:79px;height:28px;background:var(--dark);color:#fff;font-size:10px;font-weight:700;text-align:center;line-height:28px}

.footer-col{top:994px}
.footer-col h5{font-weight:400;font-size:12px;color:var(--green-text);margin-bottom:16px}
.footer-col li{list-style:none;font-size:9.4px;line-height:15.2px;color:#666}
.contact li{line-height:18.4px;color:#444}
.social{left:708px;top:994px;width:106px}
.social h5{font-weight:400;font-size:12px;color:var(--green-text)}
.social-row{position:absolute;left:0;width:106px;height:22px;font-size:9.4px;color:#444}
.social-row i{position:absolute;left:0;top:0;width:21px;height:21px;border-radius:50%;background:#fff;border:1px solid #ddd}
.social-row span{position:absolute;right:0;top:4px}

.footer-rule{left:0;top:986px;width:913px;height:1px;background:#ddd}
.bottom-bar{left:0;top:1150px;width:913px;height:50px;background:#e6e6e6;border-top:1px solid #d6d6d6;text-align:center;font-size:9px;color:#444;line-height:18px;padding-top:12px}
</style>
</head>
<body>

<header class="site-header abs"></header>
<div class="brand abs">LARKFIELD</div>
<div class="brand-sub abs">ADVISORY</div>
<div class="phone abs">Phone &nbsp;: 1-800-5521-730</div>
<div class="email abs">Email: info@larkfieldadvisory.com</div>

<nav class="main-nav abs">
  <ul><li>Home</li><li>About Us</li><li>Services</li><li>Testimonials</li><li>FAQ’s</li><li>Contact Us</li></ul>
</nav>
<div class="search abs">Type search
  <svg width="10" height="10" viewBox="0 0 10 10"><circle cx="4" cy="4" r="3" fill="none" stroke="#999" stroke-width="1.2"/><line x1="6.2" y1="6.2" x2="9" y2="9" stroke="#999" stroke-width="1.4"/></svg>
</div>

<div class="hero abs" role="img" aria-label="Sunlit forest path with tall trees and rays of light"></div>
<h1 class="hero-title abs">Anxiety <span>&amp;</span><br>Depression</h1>
<div class="dots abs"><i></i><i></i><i></i><i></i></div>

<div class="content-panel abs"></div>

<div class="service s1 abs" role="img" aria-label="Bright modern office with desks"><div class="label">Workplace Stress</div></div>
<div class="service s2 abs" role="img" aria-label="Stacked stones by the sea"><div class="label">Counselling</div></div>
<div class="service s3 abs" role="img" aria-label="Autumn leaves against blue sky"><div class="label">Anxiety &amp; Depression</div></div>

<div class="welcome abs" role="img" aria-label="Person sitting hunched on the ground in dim light"></div>
<div class="welcome-sub abs">Welcome To</div>
<div class="welcome-title abs"><span>Larkfield</span> Advisory</div>
<p class="intro abs">Sed ut perspiciatis unde omnis iste natus error sit voluptatem accusantium doloremque laudantium, totam rem aperiam, eaque ipsa quae ab illo inventore veritatis et quasi architecto beatae vitae dicta sunt explicabo. Nemo enim ipsam voluptatem quia voluptas sit aspernatur aut odit aut fugit, sed quia consequuntur magni dolores eos qui ratione voluptatem sequi nesciunt. Neque porro quisquam est, qui dolorem ipsum quia dolor sit amet, consectetur, adipisci velit, sed quia non numquam eius modi tempora incidunt ut labore et dolore magnam aliquam quaerat voluptatem. &nbsp;<b>Read More</b></p>

<aside class="news abs">
  <h3>Latest News</h3>
  <div class="news-item" style="top:48px">
    <div class="news-thumb" role="img" aria-label="Hand squeezing a yellow stress ball" style="background:linear-gradient(135deg,#f3e24a,#e0b93a 60%,#f4f4f4)"></div>
    <div class="news-body"><h4>At vero eos et accusamus</h4><p>It is a long established fact that a reader will be distracted by the readable content of a page when looking at its layout.</p><a>Read More &gt;&gt;</a></div>
  </div>
  <div class="news-item" style="top:135px">
    <div class="news-thumb" role="img" aria-label="Head silhouette on orange background" style="background:linear-gradient(90deg,#f4a21a,#222 55%,#f4a21a)"></div>
    <div class="news-body"><h4>At vero eos et accusamus</h4><p>It is a long established fact that a reader will be distracted by the readable content of a page when looking at its layout.</p><a>Read More &gt;&gt;</a></div>
  </div>
</aside>

<section class="newsletter abs"></section>
<div class="nl-title abs">Sign up for Newsletter</div>
<div class="nl-sub abs">Get a weekly Updates Through E-mail</div>
<div class="nl-input abs">Enter Your E-mail address</div>
<div class="nl-submit abs">SUBMIT</div>

<div class="footer-rule abs"></div>
<div class="footer-col abs" style="left:98px"><h5>Quick Links</h5><ul><li>Home</li><li>About Us</li><li>Services</li><li>Testimonials</li><li>FAQ’s</li><li>Contact Us</li></ul></div>
<div class="footer-col abs" style="left:282px"><h5>Support Links</h5><ul class="contact"><li>Legal Notice</li><li>Privacy Policy</li><li>Terms &amp; Conditions</li><li>Help</li></ul></div>
<div class="footer-col abs" style="left:463px"><h5>Contact Us</h5><ul class="contact"><li style="font-weight:600">Larkfield Advisory</li><li>14 Alder Lane, Westbrook Falls</li><li>Phone: 1-800-5521-730</li><li>Email: info@larkfieldadvisory.com</li><li>Website: www.larkfieldadvisory.com</li></ul></div>
<div class="social abs">
  <h5>Connect With Us</h5>
  <div class="social-row" style="top:30px"><i></i><span>Chatter</span></div>
  <div class="social-row" style="top:59px"><i></i><span>Friendsite</span></div>
  <div class="social-row" style="top:88px"><i></i><span>Worklink</span></div>
</div>

<footer class="bottom-bar abs">Copyright ©2013 Larkfield Advisory &nbsp;- All rights reserved</footer>

</body>
</html>
```